Brightwater Care Partners, LLC Business Card update!

would like a classier business card. Our cards currently just have our logo and contact information. Need better use of color and creativity
Logo attached.

Target Market(s)

Potential clients, contacts, existing clients. We are a consulting company

Industry/Entity Type

Business

Contact Information for Business Card

We like our colors but just have a boring card with our logo and a white background. I want something that stands out.

Colors
ec1f27
757575

Requirements
Must have
• Color to stay consistent. Logo provided
Nice to have
• Just better use of color/ design

```html
<!DOCTYPE html>
<html lang="en">
<head>
<meta charset="utf-8">
<title>Teslowin Care Advisory – Business Card</title>
<link rel="stylesheet" href="https://fonts.googleapis.com/css2?family=Open+Sans:wght@400;600;700&display=swap">
<style>
  :root {
    --brand-red: #ec1f27;
    --band-red: #c52026;
    --brand-grey: #757575;
    --text-grey: #5f6061;
    --card-white: #ffffff;
    --backdrop: #2b2b2b;
  }
  * { box-sizing: border-box; margin: 0; padding: 0; }
  html, body {
    width: 1200px;
    height: 900px;
    overflow: hidden;
    background: var(--backdrop);
    font-family: "Open Sans", Arial, sans-serif;
  }
  .business-card {
    position: absolute;
    left: 150px;
    top: 193px;
    width: 900px;
    height: 514px;
    background: var(--card-white);
    overflow: hidden;
  }
  .emblem-area {
    position: absolute;
    left: 50px;
    top: 40px;
    width: 400px;
    height: 400px;
    border-radius: 50%;
    background: radial-gradient(circle at 50% 50%, rgba(236,31,39,0.22) 0%, rgba(117,117,117,0.16) 55%, rgba(117,117,117,0) 72%);
  }
  .brand-lockup {
    position: absolute;
    left: 470px;
    top: 56px;
    display: flex;
    align-items: center;
    gap: 14px;
  }
  .brand-dot {
    width: 38px;
    height: 38px;
    border-radius: 50%;
    background: var(--brand-red);
    flex: none;
  }
  .brand-name {
    color: var(--brand-red);
    font-weight: 400;
    font-size: 28px;
    line-height: 1.05;
    letter-spacing: 0.3px;
  }
  .contact-block {
    position: absolute;
    right: 110px;
    top: 160px;
    text-align: right;
    color: var(--text-grey);
  }
  .owner-name {
    color: var(--band-red);
    font-weight: 700;
    font-size: 24px;
    line-height: 1.2;
  }
  .owner-role {
    font-size: 19px;
    line-height: 1.3;
  }
  .contact-list {
    list-style: none;
    margin-top: 24px;
    font-size: 19px;
    line-height: 1.5;
  }
  .contact-list li {
    position: relative;
  }
  .contact-icon {
    position: absolute;
    right: -30px;
    top: 8px;
    width: 16px;
    height: 14px;
  }
  .band-left {
    position: absolute;
    left: 0;
    top: 452px;
    width: 300px;
    height: 62px;
    background: var(--band-red);
  }
  .band-address {
    position: absolute;
    left: 440px;
    top: 404px;
    width: 460px;
    height: 110px;
    background: var(--band-red);
    color: var(--card-white);
    font-size: 19px;
    padding: 44px 0 0 50px;
    white-space: nowrap;
  }
</style>
</head>
<body>
  <main class="business-card">
    <div class="emblem-area" role="img" aria-label="Large brand emblem area"></div>

    <div class="brand-lockup">
      <span class="brand-dot"></span>
      <p class="brand-name">TESLOWIN<br>Care Advisory</p>
    </div>

    <section class="contact-block">
      <p class="owner-name">Owner Name</p>
      <p class="owner-role">Managing Director</p>
      <ul class="contact-list">
        <li>000 123 456 456
          <svg class="contact-icon" viewBox="0 0 16 14" aria-hidden="true">
            <path d="M1 4 Q8 -1 15 4 L13 6 L11 4 L5 4 L3 6 Z M4 7 L12 7 L14 13 L2 13 Z" fill="#ec1f27"/>
          </svg>
        </li>
        <li>iinfo@compnayname.com
          <svg class="contact-icon" viewBox="0 0 16 14" aria-hidden="true">
            <rect x="1" y="2" width="14" height="10" fill="#ec1f27"/>
            <path d="M1 2 L8 8 L15 2" fill="none" stroke="#fff" stroke-width="1.3"/>
          </svg>
        </li>
        <li>www.companyname.com
          <svg class="contact-icon" viewBox="0 0 16 14" aria-hidden="true">
            <g fill="none" stroke="#ec1f27" stroke-width="2">
              <rect x="1.5" y="6" width="7" height="5" rx="2.5" transform="rotate(-40 5 8.5)"/>
              <rect x="7.5" y="3" width="7" height="5" rx="2.5" transform="rotate(-40 11 5.5)"/>
            </g>
          </svg>
        </li>
      </ul>
    </section>

    <div class="band-left"></div>
    <footer class="band-address">Address line1, Address Line, Country, 012</footer>
  </main>
</body>
</html>
```